Coffee House With Cycling Theme Wants Business Cards

We want to create a business card for a coffee house that has a cycling theme. We expect to use the current logo on one side of the business card and we have been considering adding the words 'COFFEE HOUSE' underneath (see example). For the other side of the business card we want an interesting design with tag-line, address and social media links (the normal business card stuff). See examples provided but we are not fixed on having it exactly as shown, we are very open to great creative ideas. Please note our logo has the initials ‘KR' in orange embedded in the design and this must be retained. However, you can play with the words COFFEE HOUSE as well as use the orange color on the backside of the business card, as you see fit. For an image on the backside of the business card it can be a photo, hand-drawn or whatever but it must visually combine coffee and cycling in some way. The interior of the Coffee House will be reclaimed wood, rustic and have an urban feel to it with cycling artifacts hanging from the walls/ceiling, etc. Finally, it would be beneficial if the business card design elements can be easily used on flyers and other promotional assets. Good luck, we are looking forward to seeing your creative ideas.

Target Market(s)

Coffee lovers and cycling fans

Contact Information for Business Card

See project description.

Colors

Designer to choose colors to be used in the design.

Requirements
Must have
• Must use the current logo provided and combine a coffee and bike theme.
Nice to have
• Orange is used in current logo and could be used as an accent color on the backside of the business card.

```html
<!DOCTYPE html>
<html lang="en">
<head>
<meta charset="utf-8">
<title>KR Coffee House Business Cards</title>
<link href="https://fonts.googleapis.com/css2?family=Montserrat:wght@400;700&family=Questrial&display=swap" rel="stylesheet">
<style>
  :root {
    --page: #4a4c50;
    --card-dark: #3a3a3b;
    --card-light: #ffffff;
    --ink: #3b3b3d;
    --orange: #f26522;
    --white: #ffffff;
  }
  * { margin: 0; padding: 0; box-sizing: border-box; }
  html, body {
    width: 1200px; height: 960px; overflow: hidden;
    background: var(--page);
    font-family: "Questrial", "Century Gothic", sans-serif;
  }
  .canvas {
    position: relative; width: 1200px; height: 960px;
  }
  .card {
    position: absolute; left: 240px; width: 720px; height: 411px;
    border-radius: 36px; overflow: hidden;
  }
  .card--back { top: 44px; background: var(--card-dark); }
  .card--front { top: 505px; background: var(--card-light); }

  .back-brand {
    position: absolute; inset: 0;
    display: flex; align-items: center; justify-content: center;
    font-family: "Montserrat", sans-serif; font-weight: 700;
    font-size: 170px; color: var(--white); letter-spacing: 6px;
  }

  .front-brand {
    position: absolute; right: 50px; top: 42px;
    font-family: "Montserrat", sans-serif; font-weight: 700;
    font-size: 104px; line-height: 1; color: var(--orange); letter-spacing: 4px;
  }
  .rule {
    position: absolute; left: 48px; right: 44px; top: 240px;
    height: 2px; background: var(--ink);
  }
  .identity { position: absolute; left: 48px; top: 166px; }
  .identity__name {
    font-family: "Montserrat", sans-serif; font-weight: 700;
    font-size: 30px; color: var(--orange); line-height: 1.1;
  }
  .identity__title { font-size: 22px; color: var(--ink); margin-top: 4px; }

  .contacts {
    position: absolute; left: 48px; top: 262px; list-style: none;
  }
  .contacts li {
    display: flex; align-items: center; gap: 16px;
    font-size: 22px; color: var(--ink); height: 33px;
  }
  .contacts svg { width: 20px; height: 20px; flex: none; }

  .address {
    position: absolute; right: 48px; top: 262px;
    display: flex; gap: 14px; align-items: flex-start;
    font-size: 20px; color: var(--ink); line-height: 1.25;
  }
  .address svg { width: 20px; height: 26px; margin-top: 6px; flex: none; }

  .band {
    position: absolute; left: 0; right: 0; bottom: 0; height: 22px;
    background: var(--orange);
  }
</style>
</head>
<body>
<main class="canvas">
  <section class="card card--back" aria-label="Card back">
    <div class="back-brand">KR</div>
  </section>

  <section class="card card--front" aria-label="Card front">
    <div class="front-brand">KR</div>

    <div class="identity">
      <p class="identity__name">Your Name</p>
      <p class="identity__title">Your Title</p>
    </div>
    <div class="rule"></div>

    <ul class="contacts">
      <li>
        <svg viewBox="0 0 24 24"><path fill="#f26522" d="M6.6 10.8a15 15 0 0 0 6.6 6.6l2.2-2.2a1 1 0 0 1 1-.25 11.4 11.4 0 0 0 3.6.57 1 1 0 0 1 1 1V20a1 1 0 0 1-1 1A17 17 0 0 1 3 4a1 1 0 0 1 1-1h3.5a1 1 0 0 1 1 1c0 1.25.2 2.45.57 3.57a1 1 0 0 1-.25 1z"/></svg>
        123-456-2100
      </li>
      <li>
        <svg viewBox="0 0 24 24"><rect x="2" y="5" width="20" height="14" fill="#f26522"/><path d="M2 5l10 8 10-8" fill="none" stroke="#fff" stroke-width="1.8"/></svg>
        youremail@mailbox.com
      </li>
      <li>
        <svg viewBox="0 0 24 24"><circle cx="12" cy="12" r="10" fill="#f26522"/><circle cx="12" cy="12" r="4" fill="#fff"/></svg>
        www.yourwebsite.com
      </li>
    </ul>

    <div class="address">
      <svg viewBox="0 0 20 26"><path fill="#f26522" d="M10 0a10 10 0 0 0-10 10c0 7 10 16 10 16s10-9 10-16A10 10 0 0 0 10 0zm0 14a4 4 0 1 1 0-8 4 4 0 0 1 0 8z"/></svg>
      <p>Your address, city<br>state, ZIP 0000</p>
    </div>

    <div class="band"></div>
  </section>
</main>
</body>
</html>
```